Create Website for new company called "Verdale Lodge 37"

Verdale Lodge 37 is a new business situated in Southwestern Colorado. We are creating a business that will rent out spaces where clients can grow their own marijuana. Picture a large green house with partitioned spaces that are secured by a lock. Best way to envision this would be to think of a storage business that rents out storage rooms. The difference is that we will be having the units inside a green house ( for growing purposes) Picture a small area that is secured by locks, Picture an area that has the ability to provide state of the art security, cameras etc. We want to focus our efforts on professionals, blue collar workers and end users of marijuana. Our emphasis is in the area of assisting those whom wish to grow their own plants. We want to provide them a safe facility in which to do that. . Keep in mind that we also build custom grow rooms at clients homes and provide a grow pod (lease these) where a small grow unit will be delivered and picked up from our clients whom want to lease a unit for a short amount of time. We have a business card ( just designed) and will send that information to those whom express an interests in this project. We want to be able to sign people up for our services by entering an agreement and signing the agreement while on the internet. We want to provide our services to those whom consume recreational and medical marijuana. This site will need to gather information I.e email addresses so that we can followup with offers. This is a tremendous opportunity for the right designer. We will be creating many more websites as other states come on line and make marijuana legal to consume. Use the business card model for a point of reference of how we envision the concept. That is a business card we just recently printed. The hands and the plant is our logo so far. Open to suggestions. There will be three levels of service. Bronze, Silver, Gold or Platinum. We will also have a retail biz down the road but not at the present time.

Target Market(s)

Ages 21-60

Industry/Entity Type

Medical

Logo Text

Verdale Lodge 37.

Number of Pages Required

5+ page

Requirements
Must have
• Clean appearance not to busy , easily navigable from link to link, page to page. Must have ability down the road to enter into a contractual agreement via the website. Must use our provided logo and example of that is on our business card that will be uploaded here shortly. We would like to have the colors that are on the business card however if you have suggestions or color schemes that you want us to consider that is okay.
Nice to have
• Nice to have a animation of seed to weed and how clients can save a tremendous amount of money growing their own cannabis. Nice to have testimonial page or feedback page. Have a membership component to website,
Should not have
• No flashing lights, etc. Not to busy in terms of animations.

```html
<!DOCTYPE html>
<html lang="en">
<head>
<meta charset="utf-8">
<title>Verdale Lodge 37</title>
<link href="https://fonts.googleapis.com/css2?family=Oswald:wght@400;500&family=Lato:ital,wght@0,400;0,700;1,400&display=swap" rel="stylesheet">
<style>
:root{
  --green:#12873a;
  --green-dark:#0c6a2b;
  --green-light:#25a04a;
  --ink:#333;
  --muted:#777;
  --panel:#f3f3f3;
  --footer:#333;
  --footer-panel:#444;
  --field:#555;
  --white:#fff;
}
*{margin:0;padding:0;box-sizing:border-box}
html,body{width:780px;height:1200px;overflow:hidden;background:var(--white)}
body{position:relative;font-family:"Lato",sans-serif;color:var(--ink)}
h2,h3,h4{font-weight:400}
.abs{position:absolute}
.head-font{font-family:"Oswald",sans-serif}
.line{display:block;white-space:nowrap}

/* top bar */
.topbar{left:0;top:0;width:780px;height:52px;background:linear-gradient(var(--green-light),var(--green-dark))}
.topbar .phone{left:86px;top:17px;color:var(--white);font-size:16px;display:flex;align-items:center;gap:6px}
.social{display:flex;gap:6px}
.social span{width:22px;height:22px;border-radius:50%;background:var(--white);display:block}
.topbar .social{left:590px;top:15px}

/* nav */
.nav{left:0;top:52px;width:780px;height:36px;background:var(--white)}
.nav a{position:absolute;top:6px;height:25px;line-height:25px;font-family:"Oswald",sans-serif;font-size:10.5px;color:#222;text-decoration:none;padding:0 10px;border-right:1px solid #ccc}
.nav a.active{background:var(--green);color:var(--white);border:none;padding:0 15px}
.nav a.last{border-right:1px solid #f0a040}

/* logo */
.brand{left:290px;top:14px;width:200px;height:110px}
.brand .name{position:absolute;left:0;top:42px;width:200px;text-align:center;font-family:"Oswald",sans-serif;font-weight:500;font-size:21px;color:#333}

/* hero */
.hero{left:0;top:88px;width:780px;height:310px;background:radial-gradient(ellipse at 50% 40%,#6aa648,#2f6e2c 60%,#1d4a1f)}
.hero-arrow{width:28px;height:28px;border-radius:50%;border:2px solid #ddd;background:rgba(0,0,0,.35);top:228px}
.hero-caption{left:85px;top:317px;width:610px;height:38px;background:rgba(20,30,20,.7);color:var(--white);font-family:"Oswald",sans-serif;font-size:20px;line-height:36px;text-align:center}

.band-grey{left:0;top:398px;width:780px;height:209px;background:var(--panel)}

/* service cards */
.card{top:363px;width:188px;height:214px;background:var(--white);border:1px solid #c9c9c9;border-radius:6px;overflow:hidden;box-shadow:0 8px 8px -6px rgba(0,0,0,.3)}
.card h3{height:36px;line-height:36px;padding-left:13px;background:linear-gradient(var(--green-light),var(--green-dark));color:var(--white);font-family:"Oswald",sans-serif;font-size:14.5px}
.card .thumb{margin:10px 9px 0;height:78px;border:3px solid #777}
.card p{margin:8px 10px 0;font-size:9px;line-height:14.5px;color:#666}
.more{font-size:8px;font-weight:700;color:#333;text-decoration:underline;display:block}
.card .more{margin:2px 10px 0}

/* welcome */
.welcome{left:0;top:607px;width:780px;height:183px;background:linear-gradient(var(--green-light),var(--green-dark))}
.video{left:85px;top:625px;width:188px;height:146px;background:linear-gradient(#c7b9a0,#4f7d37 55%,#2f5e25)}
.video .play{position:absolute;left:82px;top:56px;width:24px;height:24px;border-radius:50%;background:var(--white)}
.video .bar{position:absolute;left:0;bottom:0;width:188px;height:19px;background:#1b1b1b;color:#ccc;font-size:7px;display:flex;align-items:center;gap:6px;padding:0 6px}
.video .track{flex:1;height:4px;background:#555;border-radius:2px}
.welcome-title{left:296px;top:622px;color:var(--white);font-family:"Oswald",sans-serif;font-size:17.5px}
.welcome-rule{left:296px;top:651px;width:399px;height:1px;background:rgba(255,255,255,.6)}
.welcome-copy{left:296px;top:661px;width:400px;color:var(--white);font-size:9.2px;line-height:15px}
.welcome-copy p+p{margin-top:14px}
.welcome-copy .more{color:var(--white);margin-top:4px}

/* testimonial & news */
.band-light{left:0;top:790px;width:780px;height:225px;background:linear-gradient(var(--white),#e5e5e5)}
.sec-title{font-family:"Oswald",sans-serif;font-size:15px;color:#333;display:flex;align-items:center;gap:8px}
.sec-rule{height:1px;background:#555}
.quote-box{left:85px;top:854px;width:280px;height:106px;background:#676767;border-radius:4px;color:var(--white);font-style:italic;font-size:8.9px;line-height:15px;padding:15px 0 0 18px;overflow:hidden}
.quote-box .first{padding-left:20px}
.quote-box .mark{position:absolute;font-family:"Oswald",sans-serif;font-size:28px;color:#bbb;font-style:normal;line-height:1}
.quote-author{left:142px;top:968px;font-size:10px;font-weight:700}
.divider{left:389px;top:845px;width:2px;height:130px;background:linear-gradient(transparent,#bbb,transparent)}
.news{left:415px;width:280px}
.news .date{font-size:8.5px;font-weight:700;display:flex;align-items:center;gap:5px}
.news .date i{width:8px;height:8px;background:#bbb;display:block}
.news h4{margin:5px 0 0 12px;font-size:10px;font-weight:700;color:#555}
.news p{margin:2px 0 0 12px;font-size:8.5px;line-height:13.5px;color:#888}

/* footer */
.footer{left:0;top:1015px;width:780px;height:185px;background:var(--footer)}
.quote-panel{left:85px;top:1018px;width:188px;height:182px;background:var(--footer-panel)}
.quote-panel h3{position:absolute;left:38px;top:10px;font-family:"Oswald",sans-serif;font-size:15.5px;color:var(--white)}
.field{position:absolute;left:12px;width:164px;height:23px;background:var(--field);border:1px solid #6a6a6a;color:#aaa;font-size:7px;padding:5px 7px}
.btn{position:absolute;background:var(--green);color:var(--white);font-size:10px;text-align:center}
.f-title{font-family:"Oswald",sans-serif;font-size:13px;color:var(--white)}
.f-text{color:#ddd;font-size:9px;line-height:13.5px}
.f-rule{height:1px;background:#555}
.f-vrule{width:1px;background:#555}
</style>
</head>
<body>

<header>
  <div class="abs topbar">
    <div class="abs phone">
      <svg width="18" height="18" viewBox="0 0 18 18" aria-hidden="true"><circle cx="9" cy="9" r="8" fill="none" stroke="#fff" stroke-width="1.5"/><path d="M6 5c-1 1 0 4 2 6s5 3 6 2l-1.5-1.5-1.5 1c-1-.5-2.5-2-3-3l1-1.5z" fill="#fff"/></svg>
      +1 970-555-0137
    </div>
    <div class="abs social"><span></span><span></span><span></span><span></span></div>
  </div>
  <nav class="abs nav">
    <a class="active" style="left:85px">HOME</a>
    <a style="left:152px">ABOUT US</a>
    <a style="left:226px;border:none">SERVICES</a>
    <a style="left:496px">FACILITIES</a>
    <a style="left:556px">TESTIMONIAL</a>
    <a class="last" style="left:627px">CONTACT US</a>
  </nav>
  <div class="abs brand">
    <svg width="200" height="110" viewBox="0 0 200 110" aria-hidden="true">
      <ellipse cx="100" cy="55" rx="99" ry="54" fill="#1b8a3d"/>
      <ellipse cx="100" cy="57" rx="93" ry="50" fill="#fff"/>
    </svg>
    <div class="name">Verdale Lodge 37</div>
  </div>
</header>

<main>
  <section class="abs hero" role="img" aria-label="Hands reaching over leafy green plants in a grow room"></section>
  <svg class="abs hero-arrow" style="left:56px" viewBox="0 0 28 28" aria-hidden="true"><path d="M16 8l-6 6 6 6" stroke="#fff" stroke-width="2" fill="none"/></svg>
  <svg class="abs hero-arrow" style="left:695px" viewBox="0 0 28 28" aria-hidden="true"><path d="M12 8l6 6-6 6" stroke="#fff" stroke-width="2" fill="none"/></svg>
  <div class="abs hero-caption">Lorem ipsum dolor sit amet, consectetuer adipiscing elit, sed</div>

  <div class="abs band-grey"></div>

  <article class="abs card" style="left:85px">
    <h3>FOR LEASE</h3>
    <div class="thumb" role="img" aria-label="Lease sign in front of a building" style="background:linear-gradient(90deg,#b9c7d6,#cfd6c8 50%,#7fa27a)"></div>
    <p><span class="line">Lorem ipsum dolor sit ametuer adipiscingi</span><span class="line">elit, sed diam nmy nibh euismod tincidunt</span><span class="line">ut laoreet dolore magna am erat visi enim</span><span class="line">ad minim veniam, quis nostrud exerci</span></p>
    <a class="more">READ MORE »</a>
  </article>
  <article class="abs card" style="left:296px">
    <h3>FOR LOCK</h3>
    <div class="thumb" role="img" aria-label="Padlock on a wooden door" style="background:linear-gradient(90deg,#4a5a4e,#9a9f98 50%,#d8d8d2)"></div>
    <p><span class="line">Lorem ipsum dolor sit ametuer adipiscingi</span><span class="line">elit, sed diam nmy nibh euismod tincidunt</span><span class="line">ut laoreet dolore magna am erat visi enim</span><span class="line">ad minim veniam, quis nostrud exerci</span></p>
    <a class="more">READ MORE »</a>
  </article>
  <article class="abs card" style="left:507px">
    <h3>FOR CAMERA</h3>
    <div class="thumb" role="img" aria-label="Security camera on a warm background" style="background:linear-gradient(#d9b089,#b57a4d 70%,#6e4a2d)"></div>
    <p><span class="line">Lorem ipsum dolor sit ametuer adipiscingi</span><span class="line">elit, sed diam nmy nibh euismod tincidunt</span><span class="line">ut laoreet dolore magna am erat visi enim</span><span class="line">ad minim veniam, quis nostrud exerci</span></p>
  </article>

  <section class="abs welcome"></section>
  <div class="abs video" role="img" aria-label="Video: an officer inspecting a room of green plants">
    <div class="play"><svg width="24" height="24" viewBox="0 0 24 24" aria-hidden="true"><path d="M10 7l7 5-7 5z" fill="#333"/></svg></div>
    <div class="bar"><svg width="8" height="8" viewBox="0 0 8 8" aria-hidden="true"><path d="M1 0l7 4-7 4z" fill="#fff"/></svg><span>04:59</span><span class="track"></span><span>10:35</span></div>
  </div>
  <h2 class="abs welcome-title">Welcome To Verdale Lodge 37</h2>
  <div class="abs welcome-rule"></div>
  <div class="abs welcome-copy">
    <p><span class="line">Lorem ipsum dolor sit amet, consectetuer adipiscing elit, sed diam nonummy nibh euismod ut laoreet</span><span class="line">dolore magna aliquam erat volutpat. Ut wisi enim ad minim veniam, quis nostrud etation ullamcorper</span><span class="line">suscipit lobortis nisl ut aliquip ex ea commodo consequat.</span></p>
    <p><span class="line">Duis autem vel eum iriure dor in hendrerit in vulputate velit esse molestie &nbsp;vel illum dolore eu feugiat</span><span class="line">nulla facilisro eros et accumsan et iusto odio dignissim qui blandit praesent luptatum zzril.</span></p>
    <a class="more">READ MORE »</a>
  </div>

  <div class="abs band-light"></div>
  <h2 class="abs sec-title" style="left:87px;top:810px">
    <svg width="18" height="16" viewBox="0 0 18 16" aria-hidden="true"><rect x="0" y="0" width="12" height="9" rx="2" fill="#1b8a3d"/><rect x="5" y="5" width="13" height="8" rx="2" fill="#1b8a3d"/></svg>
    Client Testimonial
  </h2>
  <div class="abs sec-rule" style="left:85px;top:837px;width:282px"></div>
  <div class="abs quote-box">
    <span class="mark" style="left:17px;top:14px">“</span>
    <span class="line first">Lorem ipsum dolor sit amet, consectetuer adipi sed diam nony</span>
    <span class="line">nibh euismod ut laoreet dolore magna aliquam erat volut wisi enim</span>
    <span class="line">ad minim veniam, quis nostrud etation ullamcorpecipit lobortis nisl</span>
    <span class="line">ut aliquip ex ea commodo consequatuis autem vel eum iriure dor in</span>
    <span class="line">hendrerit in vulputate velit esse molestie &nbsp;vel illum dolore <span class="mark" style="position:relative;font-size:22px;top:4px">”</span></span>
  </div>
  <svg class="abs" style="left:112px;top:959px" width="22" height="14" viewBox="0 0 22 14" aria-hidden="true"><path d="M0 0h22L20 14z" fill="#676767"/></svg>
  <div class="abs quote-author">Mr. Nisl Ut Aliquip</div>

  <div class="abs divider"></div>

  <h2 class="abs sec-title" style="left:415px;top:810px">
    <svg width="20" height="16" viewBox="0 0 20 16" aria-hidden="true"><path d="M1 5h5l9-5v16l-9-5H1z" fill="#1b8a3d"/></svg>
    Latest News
  </h2>
  <div class="abs sec-rule" style="left:415px;top:837px;width:280px"></div>
  <div class="abs news" style="top:853px">
    <div class="date"><i></i>14-March-2014</div>
    <h4>Exerci tation ullamcorper suscipit lobortis nisl ut aliquip.</h4>
    <p>Lorem ipsum dolor sit amet, consectetuer adipiscing eli sed di nonmmy nibh euismod tincidunt ut laoreet dolore ma aliquam erat volutpat.</p>
  </div>
  <div class="abs" style="left:415px;top:916px;width:280px;border-top:1px dotted #777"></div>
  <div class="abs news" style="top:929px">
    <div class="date"><i></i>14-March-2014</div>
    <h4>Mullamcorper suscipit lobortis nisl ut aliquip.</h4>
    <p>nibh euismod tincidunt ut laoreet dolore ma aliquam erat volutpat.</p>
  </div>
</main>

<footer>
  <div class="abs footer"></div>
  <form class="abs quote-panel">
    <svg class="abs" style="left:13px;top:11px" width="20" height="17" viewBox="0 0 20 17" aria-hidden="true"><path d="M1 7L10 1l9 6v9H1z" fill="none" stroke="#fff" stroke-width="1.5"/><path d="M1 7l9 6 9-6" fill="none" stroke="#fff" stroke-width="1.5"/></svg>
    <h3>Request a Quote</h3>
    <div class="field" style="top:37px">Name</div>
    <div class="field" style="top:63px">Email</div>
    <div class="field" style="top:92px;height:42px">Message</div>
    <div class="btn" style="left:12px;top:145px;width:49px;height:23px;line-height:23px">SEND</div>
  </form>

  <div class="abs f-title" style="left:296px;top:1027px">News Latter Signup</div>
  <div class="abs field" style="left:296px;top:1052px;width:184px;height:23px;font-size:7.5px;color:#ddd;padding-top:6px">Enter Your Email</div>
  <div class="abs btn" style="left:486px;top:1052px;width:55px;height:23px;line-height:23px">SUBMIT</div>
  <div class="abs f-vrule" style="left:563px;top:1038px;height:44px"></div>
  <div class="abs f-title" style="left:589px;top:1027px">Socail Connect</div>
  <div class="abs social" style="left:590px;top:1053px"><span></span><span></span><span></span><span></span></div>

  <div class="abs f-rule" style="left:296px;top:1093px;width:399px"></div>
  <svg class="abs" style="left:296px;top:1108px" width="10" height="14" viewBox="0 0 10 14" aria-hidden="true"><path d="M5 0a5 5 0 0 1 5 5c0 3-5 9-5 9S0 8 0 5a5 5 0 0 1 5-5z" fill="#fff"/><circle cx="5" cy="5" r="2" fill="#333"/></svg>
  <div class="abs f-text" style="left:314px;top:1106px;width:90px">Lorem ipsum dolor sit amet, consectetuer adipiscing eli sed di nonmmy</div>
  <svg class="abs" style="left:428px;top:1108px" width="8" height="11" viewBox="0 0 8 11" aria-hidden="true"><rect x="0.5" y="0.5" width="7" height="10" rx="1.5" fill="none" stroke="#fff"/><rect x="2" y="2" width="4" height="5" fill="#fff"/></svg>
  <div class="abs f-text" style="left:445px;top:1107px;font-size:10px">970-555-0137</div>
  <svg class="abs" style="left:427px;top:1132px" width="11" height="8" viewBox="0 0 11 8" aria-hidden="true"><rect width="11" height="8" fill="#fff"/><path d="M0 0l5.5 4L11 0" fill="none" stroke="#333"/></svg>
  <div class="abs f-text" style="left:445px;top:1130px">hello@verdalelodge37.com</div>
  <div class="abs f-vrule" style="left:563px;top:1103px;height:50px"></div>
  <div class="abs head-font" style="left:580px;top:1117px;width:125px;text-align:center;font-weight:500;font-size:15px;color:#fff">Verdale Lodge 37</div>
  <div class="abs f-rule" style="left:296px;top:1163px;width:399px"></div>
  <div class="abs f-text" style="left:305px;top:1176px">© 2014 Verdale Lodge &nbsp;| &nbsp;All Rights Reserved</div>
</footer>

</body>
</html>
```